Human Resource Consulting practice needs a business card design

We need a business card design (double sided colour) for our Human Resource (HR) consulting practice in regional New South Wales, australia. Our business name is Staff Compass. We support small and medium business across the Mid North Coast of New South Wales by providing them with outsourced HR support, services and products to help them achieve compliance with workplace legislation and across all areas of the employment lifecycle from recruitment to termination and everything in between. Our corporate colours are hot pink and black. The final design should communicate professionalism, trust, people focus.
I have attached the current (old) business card for your reference.

Target Market(s)

Business owners and high level managers

Industry/Entity Type

Business

Contact Information for Business Card

Name
Title
Phone no
Mobile no
Address
PO Box
email address
website

Colors
e34197

Requirements
Must have
• Tempate for changing business card personal details including Name, position title, mobile number, email address.
• Keep current logo and colours as per attached
• Logo must be presented in 2 colours or black only not white
Nice to have
• One side logo and graphic only other side logo and personal details
Should not have
• Should not be the same as the current version (attached) but a modern interpretation.
• Does not need a busy reverse side with our list of services as per current version. I feel this is too busy.
• No photos

```html
<!DOCTYPE html>
<html lang="en">
<head>
<meta charset="utf-8">
<title>Staff Compass – Business Card</title>
<link href="https://fonts.googleapis.com/css2?family=Lato:wght@400;700;900&display=swap" rel="stylesheet">
<style>
  :root {
    --hot-pink: #e0148f;
    --pink-light: #ec5cb4;
    --pink-deep: #c8087c;
    --ink: #111111;
    --grey-text: #555555;
    --paper: #f7f7f7;
    --backdrop: #e9e5e1;
  }
  html, body {
    margin: 0;
    width: 1200px;
    height: 1023px;
    overflow: hidden;
    background: var(--backdrop);
    font-family: "Lato", Arial, sans-serif;
  }
  .card {
    position: absolute;
    top: 350px;
    width: 530px;
    height: 322px;
    border-radius: 22px;
    overflow: hidden;
    box-shadow: 0 10px 26px rgba(0,0,0,0.22);
  }
  .card-front { left: 40px; background: var(--paper); }
  .card-back  { left: 630px; background: linear-gradient(135deg, var(--hot-pink), var(--pink-deep)); }

  .front-shapes { position: absolute; inset: 0; }

  .brand-name {
    position: absolute;
    margin: 0;
    font-weight: 900;
    line-height: 1;
    color: var(--ink);
  }
  .card-front .brand-name { left: 34px; top: 38px; font-size: 34px; }
  .brand-dot {
    display: inline-block;
    width: 10px; height: 10px;
    border-radius: 50%;
    background: var(--hot-pink);
    margin-left: 6px;
  }

  .contact-list {
    position: absolute;
    left: 34px; top: 112px;
    margin: 0; padding: 0;
    list-style: none;
    font-size: 14px;
    color: var(--grey-text);
  }
  .contact-list li { display: flex; align-items: center; gap: 9px; height: 22px; }
  .contact-list svg { width: 13px; height: 13px; fill: var(--hot-pink); }

  .postal-address {
    position: absolute;
    left: 34px; bottom: 30px;
    margin: 0;
    font-style: normal;
    font-size: 14px;
    line-height: 1.35;
    color: var(--grey-text);
  }

  .person {
    position: absolute;
    right: 30px; top: 32px;
    text-align: right;
  }
  .person-name { margin: 0; font-size: 17px; font-weight: 700; color: var(--hot-pink); }
  .person-title { margin: 4px 0 0; font-size: 14px; color: #ffffff; }

  .star-field {
    position: absolute;
    left: 0; top: 0;
    width: 62%; height: 100%;
    background: linear-gradient(90deg, rgba(255,255,255,0.22), rgba(255,255,255,0.04));
  }
  .card-back .brand-name {
    right: 40px; top: 120px;
    font-size: 54px;
    text-align: right;
  }
  .card-back .brand-dot { width: 14px; height: 14px; background: var(--ink); }
</style>
</head>
<body>

<section class="card card-front" aria-label="Business card front">
  <svg class="front-shapes" viewBox="0 0 530 322" preserveAspectRatio="none" aria-hidden="true">
    <path d="M225,0 L250,0 C330,150 420,250 500,322 L462,322 C385,258 298,160 225,0 Z" fill="var(--hot-pink)"/>
    <path d="M250,0 L530,0 L530,322 L500,322 C420,250 330,150 250,0 Z" fill="var(--ink)"/>
  </svg>

  <h1 class="brand-name">Staff Compass<span class="brand-dot"></span></h1>

  <ul class="contact-list">
    <li><svg viewBox="0 0 16 16"><rect x="1" y="1" width="14" height="14" rx="2"/><rect x="4" y="5" width="8" height="6" rx="1" fill="#fff"/></svg>02 6500 1234</li>
    <li><svg viewBox="0 0 16 16"><rect x="4" y="0" width="8" height="16" rx="2"/><rect x="5.5" y="2" width="5" height="10" fill="#fff"/></svg>0400 555 218</li>
    <li><svg viewBox="0 0 16 16"><rect x="0" y="3" width="16" height="10" rx="1"/><path d="M1 4 L8 9 L15 4" stroke="#fff" stroke-width="1.5" fill="none"/></svg>megan@staffcompass.com.au</li>
    <li><svg viewBox="0 0 16 16"><circle cx="8" cy="8" r="7.5"/><path d="M0.5 8 H15.5 M8 0.5 V15.5 M8 0.5 C4 4 4 12 8 15.5 M8 0.5 C12 4 12 12 8 15.5" stroke="#fff" stroke-width="1" fill="none"/></svg>www.staffcompass.com.au</li>
  </ul>

  <address class="postal-address">P.O. Box 210,<br>Harbour Bay,<br>NSW 2400</address>

  <div class="person">
    <p class="person-name">Megan Hale</p>
    <p class="person-title">Principal Consultant</p>
  </div>
</section>

<section class="card card-back" aria-label="Business card back">
  <div class="star-field" role="img" aria-label="Decorative field of soft pink stars"></div>
  <h2 class="brand-name">Staff<br>Compass<span class="brand-dot"></span></h2>
</section>

</body>
</html>
```